Gestaltung Mini Katalog für bayerische Polomarke
Gestaltung "Mini" Katalog für bayerische Polomarke
Zielgruppe
Unsere Marke richtet sich an den klassischen Lifestyle Kunden. 20 - 45 Jahre alt, legt Wert auf das Äussere und Kleidung.... Mag es gerne besonders, modern und chic.
Hallo,
wir planen derzeit einen kleinen Katalog von 8-10 Seiten im Format DIN A5 (kein Muss). Präsentiert wird darin die erste bayerische Polomarke K&M reitmode und die aktuellen Kollektionen an Polo-Teamshirts.
Die Fotos dazu werden in den nächsten 14 Tagen entstehen.
Wir suchen nun jemanden, der uns das ganze in eine moderne Gestaltung bringt. Für Vorschläge bitte statt der Fotos alternative Fotos einsetzen.
Unsere Marke bewegt sich im mittleren Preissegment und präsentiert eine ganz besondere Sportart. All das muss in dem Katalog rüber kommen. Neben den Produkt- und Modefotos werden klassische Polobilder integriert, um das Gefühl diesen Sports mit zu vermitteln.
Die Grundfarben sollten sich an denen von K&M reitmode orientieren: schwarz, blau, weiss.... Wobei wir für andere Farben, wenn diese passen bzw. begründet sind auch interessiert sind.

```html
<!DOCTYPE html>
<html lang="de">
<head>
<meta charset="utf-8">
<title>K&amp;M Shirts für Kinder</title>
<link rel="stylesheet" href="https://fonts.googleapis.com/css2?family=EB+Garamond:wght@400;600;700&display=swap">
<style>
  :root {
    --page-bg: #231f20;
    --band-teal: #1fb6d1;
    --accent-teal: #22b8d4;
    --text-white: #ffffff;
    --frame-teal: #27bcd6;
    --photo-white: #ffffff;
  }
  html, body {
    margin: 0;
    padding: 0;
    width: 1200px;
    height: 1200px;
    overflow: hidden;
    background: var(--page-bg);
  }
  .catalog-page {
    position: relative;
    width: 1200px;
    height: 1200px;
    background: var(--page-bg);
    font-family: "EB Garamond", Georgia, serif;
    color: var(--text-white);
  }
  .title-band {
    position: absolute;
    left: 0;
    top: 74px;
    width: 1200px;
    height: 72px;
    background: var(--band-teal);
    border-top: 4px solid #d9f3f8;
    box-sizing: border-box;
  }
  .title-band h1 {
    position: absolute;
    right: 20px;
    top: 6px;
    margin: 0;
    font-weight: 400;
    font-size: 52px;
    line-height: 1;
    color: var(--text-white);
  }
  .product-frame {
    position: absolute;
    width: 343px;
    height: 308px;
    background: var(--photo-white);
    border: 7px solid var(--frame-teal);
    box-sizing: border-box;
    display: flex;
    align-items: center;
    justify-content: center;
  }
  .product-photo {
    width: 230px;
    height: 240px;
    border-radius: 18px 18px 6px 6px;
  }
  .photo-black { background: linear-gradient(180deg, #1b1b1b, #050505); }
  .photo-navy { background: linear-gradient(180deg, #2b3565 0%, #2b3565 80%, #e6e9f2 80%); }
  .photo-polo { background: linear-gradient(180deg, #222 0%, #0a0a0a 100%); }
  .photo-pink { background: linear-gradient(180deg, #f3c9d6 0%, #f3c9d6 80%, #f4f4f4 80%); }

  .product-info {
    position: absolute;
    width: 560px;
    text-align: center;
    font-weight: 700;
  }
  .product-name { margin: 0; font-size: 26px; line-height: 1.2; }
  .product-number { margin: 6px 0 0; font-size: 23px; font-weight: 400; color: var(--accent-teal); line-height: 1.2; }
  .product-sizes { margin: 4px 0 0; font-size: 23px; line-height: 1.2; }
  .product-price { margin: 6px 0 0; font-size: 56px; color: var(--accent-teal); line-height: 1; }

  .brand-mark {
    position: absolute;
    left: 0;
    width: 1200px;
    top: 640px;
    text-align: center;
    font-size: 32px;
    font-weight: 400;
    color: var(--text-white);
  }
</style>
</head>
<body>
<main class="catalog-page">
  <header class="title-band">
    <h1>K&amp;M Shirts für Kinder</h1>
  </header>

  <div class="product-frame" style="left:135px; top:175px;">
    <div class="product-photo photo-black" role="img" aria-label="Schwarzes Kindershirt mit blauen Polospielern"></div>
  </div>
  <div class="product-frame" style="left:731px; top:175px;">
    <div class="product-photo photo-navy" role="img" aria-label="Dunkelblaues Babyshirt mit weißen Ärmeln und blauen Polospielern"></div>
  </div>
  <div class="product-frame" style="left:135px; top:693px;">
    <div class="product-photo photo-polo" role="img" aria-label="Schwarzes langärmeliges Team-Poloshirt mit Nummer 3"></div>
  </div>
  <div class="product-frame" style="left:752px; top:693px;">
    <div class="product-photo photo-pink" role="img" aria-label="Rosa Babyshirt mit pinken Polospielern"></div>
  </div>

  <section class="product-info" style="left:28px; top:516px;">
    <p class="product-name">Kindershirt mit Polospielern</p>
    <p class="product-number">Best.-Nr.: 080302</p>
    <p class="product-sizes">Größen: 92 - 104 - 116 - 128 - 146 - 164</p>
    <p class="product-price">29,95 €</p>
  </section>

  <section class="product-info" style="left:626px; top:516px;">
    <p class="product-name">Babyshirt</p>
    <p class="product-number">Best.-Nr.: 080303</p>
    <p class="product-sizes">Größen: 3-6 - 6-12 - 12-18 Monate</p>
    <p class="product-price">29,95 €</p>
  </section>

  <section class="product-info" style="left:28px; top:1030px;">
    <p class="product-name">Original Team Shirt 2008 Kinder langärmelig</p>
    <p class="product-number">Best.-Nr.: 080805</p>
    <p class="product-sizes">Größen: 104 - 116 - 128 - 146 - 164</p>
    <p class="product-price">49,00 €</p>
  </section>

  <section class="product-info" style="left:626px; top:1030px;">
    <p class="product-name">Babyshirt</p>
    <p class="product-number">Best.-Nr.: 080303</p>
    <p class="product-sizes">Größen: 3-6 - 6-12 - 12-18 Monate</p>
    <p class="product-price">29,95 €</p>
  </section>

  <div class="brand-mark">K&amp;M reitmode</div>
</main>
</body>
</html>
```